SkyvornQ Business Cards and Stationary Design

Need a design for our business cards and stationary. I want to carry on the theme of the logo. I want the business cards to have a design on the back. I would like the business cards and the stationary to carry the same theme, design scheme, and branding

Target Market(s)

Airlines and Maintenance Facilities

Industry/Entity Type

Aviation

Contact Information for Business Card

Name
Position Title
Address: 4827 Trellis Hollow Road, Larkmoor Bay, Oregon, 97451
Office Number
Mobile Number
Email
Website

Font styles to use
Serif
Sans Serif

Colors

Designer to choose colors to be used in the design.

```html
<!DOCTYPE html>
<html lang="en">
<head>
<meta charset="utf-8">
<title>SkyvornQ Business Card</title>
<link href="https://fonts.googleapis.com/css2?family=Exo+2:wght@500;600;700;800&display=swap" rel="stylesheet">
<style>
  :root {
    --backdrop: #2e2e2e;
    --navy: #0b2850;
    --navy-deep: #082247;
    --glow: #1aa3e8;
    --mid-blue: #0f4f9a;
    --paper: #f1f1f1;
    --ink: #0d2a52;
    --white: #ffffff;
  }
  * { margin: 0; padding: 0; box-sizing: border-box; }
  html, body { width: 1200px; height: 960px; overflow: hidden; }
  body { background: var(--backdrop); position: relative; font-family: "Exo 2", sans-serif; }

  .card {
    position: absolute;
    width: 600px;
    height: 343px;
    border-radius: 22px;
    overflow: hidden;
  }
  .card-front {
    left: 313px; top: 113px;
    background:
      radial-gradient(circle at 290px 130px, var(--glow) 0, var(--mid-blue) 110px, var(--navy) 230px, var(--navy-deep) 340px);
  }
  .card-back {
    left: 311px; top: 472px;
    background: var(--paper);
  }

  .front-brand {
    position: absolute;
    right: 26px; top: 26px;
    font-family: "Exo 2", sans-serif;
    font-weight: 800;
    font-size: 30px;
    letter-spacing: 4px;
    color: var(--white);
  }

  .holder { position: absolute; left: 35px; top: 138px; color: var(--white); }
  .holder-name { font-size: 20px; font-weight: 700; letter-spacing: 0.3px; line-height: 1.1; }
  .holder-title { font-size: 14px; font-weight: 500; letter-spacing: 0.5px; margin-top: 2px; }
  .holder-address { font-size: 13px; font-weight: 600; line-height: 18px; margin-top: 12px; letter-spacing: 0.4px; }

  .contact-list { list-style: none; margin-top: 11px; }
  .contact-list li {
    display: flex; align-items: center;
    font-size: 13px; font-weight: 600; height: 19.5px; letter-spacing: 0.4px;
  }
  .contact-icon { width: 13px; height: 13px; margin-right: 10px; fill: var(--white); }

  .back-mark {
    position: absolute;
    left: 246px; top: 94px;
    width: 108px; height: 108px;
    border-radius: 50%;
    border: 7px solid var(--mid-blue);
  }
  .back-brand {
    position: absolute;
    left: 0; right: 0; top: 212px;
    text-align: center;
    font-family: "Exo 2", sans-serif;
    font-weight: 800;
    font-size: 38px;
    letter-spacing: 8px;
    color: var(--ink);
  }
</style>
</head>
<body>

<section class="card card-front" aria-label="Business card front">
  <div class="front-brand">SKYVORNQ</div>

  <div class="holder">
    <div class="holder-name">MARCUS DELANEY</div>
    <div class="holder-title">CEO/FOUNDER</div>
    <div class="holder-address">4827 Trellis Hollow Road<br>Larkmoor Bay, Oregon, 97451</div>

    <ul class="contact-list">
      <li>
        <svg class="contact-icon" viewBox="0 0 16 16" aria-hidden="true"><path d="M3.5 1l2.5 3-1.5 1.6c.8 2 2.4 3.6 4.4 4.4L10.5 8.5l3 2.5-1.6 2.6C7 13 3 9 2.4 3z"/></svg>
        555 014 2781
      </li>
      <li>
        <svg class="contact-icon" viewBox="0 0 16 16" aria-hidden="true"><path d="M4.5 0h7a1 1 0 0 1 1 1v14a1 1 0 0 1-1 1h-7a1 1 0 0 1-1-1V1a1 1 0 0 1 1-1zm.8 2v10.5h5.4V2zM8 13.4a.9.9 0 1 0 0 1.8.9.9 0 0 0 0-1.8z"/></svg>
        555 019 6430
      </li>
      <li>
        <svg class="contact-icon" viewBox="0 0 16 16" aria-hidden="true"><path d="M1 3.5h14v9H1zm1.4 1.2L8 9l5.6-4.3z"/></svg>
        info@skyvornq.com
      </li>
      <li>
        <svg class="contact-icon" viewBox="0 0 16 16" aria-hidden="true"><path d="M8 1a7 7 0 1 0 0 14A7 7 0 0 0 8 1zm-1 12.4A5.5 5.5 0 0 1 3 5l2.5 2.5v1L7 10zm4.3-1.5L10 10.5H8.5V9L7 7.5 9 5.5V3.2a5.5 5.5 0 0 1 2.3 8.7z"/></svg>
        www.skyvornq.com
      </li>
    </ul>
  </div>
</section>

<section class="card card-back" aria-label="Business card back">
  <div class="back-mark"></div>
  <div class="back-brand">SKYVORNQ</div>
</section>

</body>
</html>
```